Patent Law

Need to develop a home page for a patent lawyer.

Colors should go with logo, blues...

Company Name- Velun Tresk, PLLC

Company Overview-

I am an Intellectual Property Lawyer and focus on patents, copyrights, trademarks, & trade secrets. I work with small businesses and start ups in the chemical and biotech industries.

Why Us-

I am small firm that can provide large-firm service at a reasonable price. I also can charge flat-fees for entreprenuers in certain practice areas.

Services-
Intellectual Property
Patents
Copyrights
Trademarks
Trade secrets
Healthcare Compliance
Elder law
Wills
Trusts

Website we like-
http://www.quorvantlegal.example/ - within industry!!
http://www.daltrowemiko.example/
http://ulbrixtane.example/
http://thegravelcounsel.example/

Target Market(s)

My customers will be small business, specifically small start-up companies in the chemical and biotech arena.

Industry/Entity Type

Trade

Requirements
Must have
• Colors should go with logo, blues...

```html
<!DOCTYPE html>
<html lang="en">
<head>
<meta charset="utf-8">
<title>Velun Tresk, PLLC — Intellectual Property Law</title>
<link href="https://fonts.googleapis.com/css2?family=Arimo:wght@400;700&display=swap" rel="stylesheet">
<style>
:root{
  --page:#f0f0f0;
  --topbar:#555555;
  --blue:#1a8ae6;
  --blue-dark:#0f6db8;
  --blue-light:#2f94dc;
  --text:#6a6a6a;
  --text-soft:#7a7a7a;
  --line:#c9c9c9;
  --tabs:#e0e1e2;
  --white:#ffffff;
  --footer:#323232;
}
*{margin:0;padding:0;box-sizing:border-box}
html,body{width:1116px;height:1200px;overflow:hidden;background:var(--page)}
body{font-family:"Arimo",Arial,sans-serif;color:var(--text)}
.site{position:relative;width:1020px;height:1097px;transform:scale(1.0941);transform-origin:0 0;background:var(--page)}
.abs{position:absolute}

.top-strip{left:0;top:0;width:1020px;height:8px;background:var(--topbar)}

.brand{left:70px;top:58px;display:flex;align-items:center;gap:10px}
.brand-mark{width:22px;height:22px;border-radius:50%;background:var(--blue-dark)}
.brand-name{font-size:15px;font-weight:400;letter-spacing:1px;color:#3a3a3a;text-transform:uppercase}

.social{left:830px;top:32px;display:flex;gap:7px}
.social span{width:25px;height:25px;border-radius:4px;background:var(--blue-light);display:block}

.contact{left:830px;top:69px;font-size:11px;letter-spacing:1px;color:#555;line-height:14px}
.contact-row{display:flex;gap:6px;align-items:flex-start}
.contact-row svg{flex:none;margin-top:1px}
.contact .phone{color:var(--blue)}
.contact-row + .contact-row{margin-top:4px}

.nav{left:0;top:136px;width:1020px;height:39px;background:linear-gradient(#2f94dc,var(--blue-dark))}
.nav a{position:absolute;top:12px;font-size:13px;letter-spacing:1px;color:var(--white);text-decoration:none;text-transform:uppercase}
.nav a.current{top:8px;left:57px;width:61px;height:23px;line-height:23px;text-align:center;background:rgba(255,255,255,.28);border-radius:2px}
.search{position:absolute;left:806px;top:8px;width:165px;height:23px;display:flex}
.search-field{width:113px;background:var(--white);font-size:13px;color:#9a9a9a;padding:4px 11px;letter-spacing:.5px}
.search-btn{width:52px;background:linear-gradient(#9c9c9c,#6c6c6c);display:flex;align-items:center;justify-content:center}

.slider{left:41px;top:205px;width:938px;height:352px;background:var(--white);box-shadow:0 14px 18px -12px rgba(0,0,0,.18)}
.slide{left:11px;top:9px;width:915px;height:270px;background:radial-gradient(ellipse at 50% 40%,#ffffff 40%,#e8e8e8 100%)}
.slide-image{left:88px;top:24px;width:125px;height:227px;border-radius:60px 60px 12px 12px;background:linear-gradient(#f4f4f4,#d6d6d6 60%,#6f6f6f)}
.slide-title{left:391px;top:52px;font-size:26px;font-weight:700;letter-spacing:3px;color:var(--blue)}
.slide-text{left:390px;top:92px;width:472px;font-size:13px;line-height:18px;letter-spacing:1px;color:var(--text)}
.slide-text a{color:var(--blue);display:block;line-height:14px}
.tabs{left:11px;top:279px;width:915px;height:64px;background:var(--tabs)}
.tab{position:absolute;top:20px;font-size:11px;line-height:14px;letter-spacing:.3px;color:var(--text-soft);text-align:center;text-transform:uppercase;transform:translateX(-50%);white-space:nowrap}
.tab.active{top:0;left:350px;width:90px;height:64px;padding-top:20px;background:var(--white);color:var(--blue);transform:none;letter-spacing:0}
.tab-pointer{left:390px;top:250px}

.features{left:41px;top:590px;width:938px;height:405px;border:1px solid #dcdcdc;border-radius:3px;background:#ececec;box-shadow:0 14px 18px -12px rgba(0,0,0,.16)}
.card{top:46px;width:275px}
.card-bar{height:8px;background:var(--blue);position:relative;width:270px}
.card-bar::after{content:"";position:absolute;left:130px;top:8px;border:6px solid transparent;border-top-color:var(--blue)}
.card-image{width:270px;height:179px}
.card-title{margin-top:14px;font-size:15px;font-weight:700;letter-spacing:1px;color:var(--blue);text-transform:uppercase}
.card-text{margin:11px 0 0 2px;width:269px;height:53px;font-size:12px;line-height:15px;letter-spacing:.7px;color:var(--text);text-align:justify}
.card-foot{position:relative;height:24px;margin-top:8px}
.card-foot::before{content:"";position:absolute;left:2px;right:0;top:11px;border-top:1px solid var(--line)}
.read-more{position:absolute;left:93px;top:0;width:74px;height:23px;line-height:23px;text-align:center;font-size:12px;letter-spacing:.8px;color:var(--white);border-radius:3px;background:linear-gradient(#3aa2f0,#1178cf);text-decoration:none}

.footer{left:0;top:1055px;width:1020px;height:42px;background:var(--footer);font-size:11px;letter-spacing:1px;color:#e6e6e6}
.footer .copy{position:absolute;left:79px;top:16px}
.footer .links{position:absolute;right:66px;top:16px;word-spacing:2px}
.footer .links span{margin:0 10px;color:#aaa}
</style>
</head>
<body>
<div class="site">
  <div class="abs top-strip"></div>

  <header>
    <div class="abs brand">
      <span class="brand-mark"></span>
      <span class="brand-name">Velun Tresk, PLLC</span>
    </div>
    <div class="abs social" aria-label="Social links">
      <span></span><span></span><span></span><span></span>
    </div>
    <div class="abs contact">
      <div class="contact-row">
        <svg width="16" height="16" viewBox="0 0 16 16" aria-hidden="true"><path d="M4 1 L6.5 4 L5 6 C6 8.5 7.5 10 10 11 L12 9.5 L15 12 L13 15 C7 14.5 1.5 9 1 3 Z" fill="#1a8ae6"/></svg>
        <div>CALL US TODAY<br><span class="phone">(05)-8810-47263</span></div>
      </div>
      <div class="contact-row">
        <svg width="16" height="18" viewBox="0 0 16 18" aria-hidden="true"><path d="M8 1 C4 1 2 4 2 7 C2 11 8 17 8 17 C8 17 14 11 14 7 C14 4 12 1 8 1 Z" fill="#1a8ae6"/><circle cx="8" cy="7" r="2.4" fill="#f0f0f0"/></svg>
        <div>MAP &amp; DIRECTIONS</div>
      </div>
    </div>
  </header>

  <nav class="abs nav">
    <a class="current" href="#">Home</a>
    <a href="#" style="left:156px">About Us</a>
    <a href="#" style="left:277px">Services</a>
    <a href="#" style="left:402px">Latest News</a>
    <a href="#" style="left:557px">Contact Us</a>
    <div class="search">
      <div class="search-field">Search</div>
      <div class="search-btn">
        <svg width="16" height="14" viewBox="0 0 16 14" aria-hidden="true"><circle cx="5.5" cy="5.5" r="3.8" fill="none" stroke="#222" stroke-width="2"/><path d="M8.5 8 L14 12.5" stroke="#222" stroke-width="2.6" stroke-linecap="round"/></svg>
      </div>
    </div>
  </nav>

  <section class="abs slider">
    <div class="abs slide">
      <div class="abs slide-image" role="img" aria-label="Glowing incandescent light bulb"></div>
      <h1 class="abs slide-title">INTELLECTUAL PROPERTY LAW</h1>
      <p class="abs slide-text">Intellectual property is the area of law that deals with protecting the rights of those who create original works. The purpose of intellectual property laws are to encourage new technologies, artistic expressions and inventions while promoting economic growth.<a href="#"><u>Learn more</u></a></p>
    </div>
    <svg class="abs tab-pointer" width="32" height="30" viewBox="0 0 32 30" aria-hidden="true"><path d="M0 30 L16 0 L32 30 Z" fill="#ffffff"/></svg>
    <div class="abs tabs">
      <div class="tab" style="left:85px">Intellectual<br>Property</div>
      <div class="tab" style="left:198px">Healthcare<br>Compliance</div>
      <div class="tab" style="left:294px">Trade<br>Secrets</div>
      <div class="tab active">Trademarks</div>
      <div class="tab" style="left:507px">Copyrights</div>
      <div class="tab" style="left:606px">Patents</div>
      <div class="tab" style="left:696px">Elder<br>Law</div>
      <div class="tab" style="left:772px">Wills</div>
      <div class="tab" style="left:844px">Trusts</div>
    </div>
  </section>

  <section class="abs features">
    <article class="abs card" style="left:35px">
      <div class="card-bar"></div>
      <div class="card-image" role="img" aria-label="Blue jigsaw puzzle with one piece missing" style="background:linear-gradient(160deg,#5e8fc4,#2c5d98 55%,#16386a)"></div>
      <h2 class="card-title">About Velun Tresk</h2>
      <p class="card-text">I am an Intellectual Property Lawyer and focus on patents, copyrights, trademarks, &amp; trade secrets<br>...</p>
      <div class="card-foot"><a class="read-more" href="#">read more</a></div>
    </article>
    <article class="abs card" style="left:330px">
      <div class="card-bar"></div>
      <div class="card-image" role="img" aria-label="Lit energy-saving bulb among unlit bulbs" style="background:radial-gradient(ellipse at 55% 35%,#b4c0de,#5d6f9e 55%,#2f3d62)"></div>
      <h2 class="card-title">Why Us?</h2>
      <p class="card-text">Lorem ipsum dolor sit amet, consectetur adipiscing elit. Curabitur lacinia pretium risus ac euismod.</p>
      <div class="card-foot"><a class="read-more" href="#">read more</a></div>
    </article>
    <article class="abs card" style="left:627px">
      <div class="card-bar"></div>
      <div class="card-image" role="img" aria-label="Newspaper with a cup of coffee and keyboard" style="background:linear-gradient(170deg,#3a3a3a,#9a9a9a 30%,#e6e4e0 55%,#d0ccc6)"></div>
      <h2 class="card-title">Latest News</h2>
      <p class="card-text">Lorem ipsum dolor sit amet, consectetur adipiscing elit. Curabitur lacinia.</p>
      <div class="card-foot"><a class="read-more" href="#">read more</a></div>
    </article>
  </section>

  <footer class="abs footer">
    <div class="copy">Copyright 2013 · All rights reserved</div>
    <div class="links">Sitemap<span>|</span>FAQ<span>|</span>Privacy Policy</div>
  </footer>
</div>
</body>
</html>
```